Parcelwise HQ letterhead and envelope

Design a formal (8.5x11) letterhead and envelope for sales outreach and legal matters. Using design input from https://www.parcelwisehq.example/ and the attached documents.

Industry/Entity Type

Software Service

Requirements
Must have
• These 4 hex colors are our official colors:
• #355c98 [blue]
• #1eb1a2 [teal]
• #fdba12 [gold]
• #f1653b [orange]
• So no other colors besides these should be used.

```html
<!DOCTYPE html>
<html lang="en">
<head>
<meta charset="utf-8">
<title>Parcelwise HQ Letterhead</title>
<link href="https://fonts.googleapis.com/css2?family=Montserrat:wght@300;600&family=Open+Sans:wght@400;600&family=Arimo:wght@700&display=swap" rel="stylesheet">
<style>
  :root{
    --blue:#355c98;
    --teal:#1eb1a2;
    --gold:#fdba12;
    --orange:#f1653b;
    --ink:#3c3c3c;
    --muted:#6b6b6b;
    --paper:#ffffff;
    --backdrop:#eeeff1;
  }
  *{margin:0;padding:0;box-sizing:border-box}
  html,body{width:1200px;height:784px;overflow:hidden;background:var(--backdrop)}
  .canvas{position:relative;width:1200px;height:784px}
  .letterhead{
    position:absolute;left:314px;top:22px;width:572px;height:740px;
    background:var(--paper);box-shadow:0 2px 10px rgba(0,0,0,.08);
    padding:58px 62px 40px 70px;font-family:"Open Sans",Arial,sans-serif;color:var(--ink);
  }
  .masthead{display:flex;justify-content:space-between;align-items:flex-start}
  .brand{display:flex;align-items:center;gap:8px;margin-top:16px}
  .brand-dot{width:20px;height:20px;border-radius:50%;background:var(--blue)}
  .brand-name{font-family:"Montserrat",sans-serif;font-weight:300;font-size:25px;color:var(--blue);letter-spacing:.3px}
  .contact{display:flex;gap:10px;font-size:6.4px;line-height:10px;color:var(--muted)}
  .contact-list{list-style:none}
  .contact-list li{display:flex;align-items:center;gap:4px}
  .contact-icon{width:7px;height:7px;border-radius:50%;background:var(--blue);display:inline-flex;align-items:center;justify-content:center}
  .contact-divider{width:1px;background:#c9d1de}
  .office-name{font-weight:600;color:var(--blue);font-size:6.8px}
  .salutation{font-family:"Arimo",Arial,sans-serif;font-weight:700;font-size:11.5px;color:#222;margin:44px 0 8px}
  .body-copy{width:400px;font-size:9.2px;line-height:13px;color:var(--ink)}
  .body-copy p{margin-bottom:13px}
  .signature{width:96px;height:46px;margin-top:18px;background:linear-gradient(90deg,#e9e9ec,#f5f5f7);border-radius:3px}
  .icon-field{position:absolute;right:30px;top:150px;width:150px;height:420px;
    background:linear-gradient(180deg,rgba(253,186,18,.05),rgba(30,177,162,.04));border-radius:6px}
</style>
</head>
<body>
<div class="canvas">
  <article class="letterhead">
    <div class="icon-field" role="img" aria-label="Faint line-icon pattern in gold and teal"></div>
    <header class="masthead">
      <div class="brand">
        <span class="brand-dot"></span>
        <span class="brand-name">Parcelwise HQ</span>
      </div>
      <div class="contact">
        <ul class="contact-list">
          <li><span class="contact-icon"><svg width="5" height="5" viewBox="0 0 10 10"><path d="M2 1l2 2-1 1.5a6 6 0 0 0 2.5 2.5L7 6l2 2-1.5 1.5C4 9 1 6 .5 2.5z" fill="#fff"/></svg></span>(800) 555-0142</li>
          <li><span class="contact-icon"><svg width="5" height="5" viewBox="0 0 10 10"><rect x="1" y="2.5" width="8" height="5" fill="none" stroke="#fff"/><path d="M1 2.5l4 3 4-3" fill="none" stroke="#fff"/></svg></span>hello@parcelwisehq.example</li>
          <li><span class="contact-icon"><svg width="5" height="5" viewBox="0 0 10 10"><circle cx="5" cy="5" r="3.8" fill="none" stroke="#fff"/><path d="M1 5h8M5 1v8" stroke="#fff"/></svg></span>www.parcelwisehq.example</li>
        </ul>
        <span class="contact-divider"></span>
        <address class="contact-list" style="font-style:normal">
          <div class="office-name">Parcelwise HQ</div>
          <div>210 Harbor Lane</div>
          <div>Riverton, OR 97001</div>
        </address>
      </div>
    </header>

    <p class="salutation">Dear Mr. Harlow,</p>
    <section class="body-copy">
      <p>Lorem Ipsum is simply dummy text of the printing and typesetting industry. Lorem Ipsum has been the industry's standard dummy text ever since the 1500s, when an unknown printer took a galley of type and scrambled it to make a type specimen book. It has survived not only five centuries, but also the leap into electronic typesetting, remaining essentially unchanged.</p>
      <p>The standard chunk of Lorem Ipsum used since the 1500s is reproduced below for those interested. Sections 1.10.32 and 1.10.33 from "de Finibus Bonorum et Malorum" by Cicero are also reproduced in their exact original form, accompanied by English versions from the 1914 translation by H. Rackham.</p>
      <p>Lorem Ipsum is simply dummy text of the printing and typesetting industry. Lorem Ipsum has been the industry's standard dummy text ever since the 1500s, when an unknown printer took a galley of type and scrambled it to make a type specimen book. It has survived not only five centuries, but also the leap into electronic typesetting, remaining essentially unchanged. It was popularised in the</p>
      <p>The standard chunk of Lorem Ipsum used since the 1500s is reproduced below for those interested. Sections 1.10.32 and 1.10.33 from "de Finibus Bonorum et Malorum" by Cicero are also reproduced in their exact original form, accompanied by English versions from the 1914 translation by H. Rackham.</p>
      <p>The standard chunk of Lorem Ipsum used since the 1500s is reproduced below for those interested. Sections 1.10.32 and 1.10.33 from "de Finibus Bonorum et Malorum" by Cicero are also reproduced in their exact original form.</p>
    </section>
    <div class="signature" role="img" aria-label="Handwritten signature"></div>
  </article>
</div>
</body>
</html>
```